Classy, Elegant, Simple Business Card Design

Looking to have a classy, simple, and elegant design. Want a top notch designed business card. I really like the look of the new torvane credit card. I also like the design I attached. I am trying to reach 21-29 year old females for booking us for there wedding or event. We offer Disc Jockey Service, Photo Booth Rentals, and Uplighting .

Target Market(s)

21-28 year old females

Contact Information for Business Card

Has to have logo, website, email, and phone number

Font styles to use
Other font styles liked:
• open to font choice, modern, clean
Designer to choose
33a6d7
0791cd
0555a3
ffffff

Requirements
Must have
• Has to have logo, website, email, and phone number
Nice to have
• I really like the design of the new torvane credit card. I also included my logo and some designs I like
Should not have
• clutter or too much info

```html
<!DOCTYPE html>
<html lang="en">
<head>
<meta charset="UTF-8">
<title>Brightline Event Group – Business Card</title>
<link rel="stylesheet" href="https://fonts.googleapis.com/css2?family=Jost:wght@400;500;600&display=swap">
<style>
  :root {
    --sky: #33a6d7;
    --blue: #0791cd;
    --royal: #0555a3;
    --navy: #0b2f63;
    --navy-deep: #082552;
    --white: #ffffff;
    --ink: #0f2f5c;
    --grey: #8a8f98;
    --stage: #e9ecf0;
  }
  * { box-sizing: border-box; margin: 0; padding: 0; }
  html, body { width: 1200px; height: 900px; overflow: hidden; }
  body {
    background: var(--stage);
    font-family: "Jost", sans-serif;
    position: relative;
  }
  .card {
    position: absolute;
    left: 250px;
    width: 700px;
    height: 400px;
    overflow: hidden;
    box-shadow: 0 10px 30px rgba(10, 30, 60, 0.18);
  }
  .card--front { top: 40px; background: var(--white); }
  .card--back { top: 470px; background: linear-gradient(135deg, var(--navy-deep), var(--navy)); }

  .pattern {
    position: absolute;
    border-radius: 50%;
  }
  .card--front .pattern {
    left: -60px; top: -40px; width: 460px; height: 460px;
    background: radial-gradient(circle, rgba(200,203,208,0.55) 0%, rgba(220,222,226,0.35) 45%, rgba(255,255,255,0) 70%);
  }
  .card--back .pattern {
    right: -80px; top: -40px; width: 520px; height: 520px;
    background: radial-gradient(circle, rgba(30,90,170,0.55) 0%, rgba(20,70,140,0.3) 45%, rgba(11,47,99,0) 70%);
  }

  .brand {
    position: absolute;
    display: flex;
    align-items: center;
    gap: 12px;
  }
  .brand__dot {
    width: 18px; height: 18px;
    border-radius: 50%;
    background: var(--blue);
    flex-shrink: 0;
  }
  .brand__name {
    font-weight: 500;
    font-size: 30px;
    letter-spacing: 2px;
    text-transform: uppercase;
    line-height: 1.1;
  }
  .card--front .brand { left: 70px; top: 160px; }
  .card--front .brand__name { color: var(--royal); }
  .card--back .brand { right: 70px; top: 170px; }
  .card--back .brand__name { color: var(--white); }

  .band {
    position: absolute;
    bottom: 0;
    height: 22px;
    background: var(--blue);
  }
  .card--front .band { left: 0; width: 230px; }
  .card--back .band { right: 0; width: 380px; }

  .contact {
    position: absolute;
    left: 400px;
    top: 120px;
    width: 260px;
    color: var(--ink);
  }
  .contact__name {
    font-weight: 600;
    font-size: 26px;
    letter-spacing: 1px;
    text-transform: uppercase;
    text-align: center;
  }
  .contact__divider {
    display: flex;
    align-items: center;
    gap: 8px;
    margin: 14px 0 18px;
  }
  .contact__rule { flex: 1; height: 2px; background: var(--blue); }
  .contact__icon {
    width: 22px; height: 22px;
    border-radius: 5px;
    background: var(--blue);
    display: flex; align-items: center; justify-content: center;
  }
  .contact__list { list-style: none; font-size: 18px; line-height: 1.55; }

  .web {
    position: absolute;
    left: 60px; top: 60px;
    color: var(--white);
    font-size: 20px;
    letter-spacing: 0.5px;
  }
  .web__accent { color: var(--sky); font-weight: 500; }
</style>
</head>
<body>
  <section class="card card--front" aria-label="Card front">
    <div class="pattern" role="img" aria-label="Soft grey radiating square pattern decoration"></div>
    <div class="brand">
      <span class="brand__dot"></span>
      <span class="brand__name">Brightline<br>Event Group</span>
    </div>
    <div class="contact">
      <h1 class="contact__name">Dane Holloway</h1>
      <div class="contact__divider">
        <span class="contact__rule"></span>
        <span class="contact__icon">
          <svg width="14" height="14" viewBox="0 0 24 24"><path fill="#fff" d="M6.6 10.8a15 15 0 0 0 6.6 6.6l2.2-2.2a1 1 0 0 1 1-.25 11.4 11.4 0 0 0 3.6.57 1 1 0 0 1 1 1V20a1 1 0 0 1-1 1A17 17 0 0 1 3 4a1 1 0 0 1 1-1h3.5a1 1 0 0 1 1 1c0 1.25.2 2.45.57 3.57a1 1 0 0 1-.25 1z"/></svg>
        </span>
        <span class="contact__icon">
          <svg width="14" height="14" viewBox="0 0 24 24"><rect x="3" y="5" width="18" height="14" rx="1" fill="none" stroke="#fff" stroke-width="2"/><path d="M3 6l9 7 9-7" fill="none" stroke="#fff" stroke-width="2"/></svg>
        </span>
        <span class="contact__icon">
          <svg width="14" height="14" viewBox="0 0 24 24"><circle cx="12" cy="12" r="9" fill="none" stroke="#fff" stroke-width="2"/><path d="M3 12h18M12 3c3 3 3 15 0 18M12 3c-3 3-3 15 0 18" fill="none" stroke="#fff" stroke-width="1.6"/></svg>
        </span>
        <span class="contact__rule"></span>
      </div>
      <ul class="contact__list">
        <li>0000 412 587</li>
        <li>hello@brightlineevents.com</li>
        <li>www.brightlineevents.com</li>
      </ul>
    </div>
    <div class="band"></div>
  </section>

  <section class="card card--back" aria-label="Card back">
    <div class="pattern" role="img" aria-label="Faint blue radiating square pattern decoration"></div>
    <p class="web">www.<span class="web__accent">brightlineevents</span>.com</p>
    <div class="brand">
      <span class="brand__dot"></span>
      <span class="brand__name">Brightline<br>Event Group</span>
    </div>
    <div class="band"></div>
  </section>
</body>
</html>
```